Kestrel Bathrooms Facelift. Moving the business in to the next professional level.

I'm currently revamping my bathroom renovation business. Part of this revamp includes our marketing strategy to better position ourselves as a professional business. As the name suggests, we primarily do bathroom renovations of all shapes, sizes and budgets. I'd like a business card design that is simple, yet displays our company as sophisticated.
What I'd like is to have a card that incorporates the following elements;
- Orange set as the primary colour and Charcoal/Grey as a complement colour. The card can also include white and/or black.
- I'd like a hexagon pattern within the charcoal/grey (In gloss perhaps to break it up a bit)
- I only want the Kestrel Bathrooms logo on the front of the card
- Back of the card would include contact details
- The bottom edges of the card would be rounded off
- I've attached the company name. I'd like to keep kestrel as it is. Bathrooms can be modified

```html
<!DOCTYPE html>
<html lang="en">
<head>
<meta charset="utf-8">
<title>Kestrel Bathrooms – Business Card</title>
<link href="https://fonts.googleapis.com/css2?family=Exo+2:wght@400;500;600&display=swap" rel="stylesheet">
<style>
  :root {
    --orange: #e5762f;
    --ink: #111111;
    --paper: #ffffff;
    --paper-back: #f9f9fb;
    --stage: #e6e6e6;
    --white: #ffffff;
  }
  * { margin: 0; padding: 0; box-sizing: border-box; }
  html, body {
    width: 1189px; height: 1200px; overflow: hidden;
    background: var(--stage);
    font-family: "Exo 2", sans-serif;
  }
  .card {
    position: absolute;
    left: 171px;
    width: 855px; height: 486px;
    box-shadow: 6px 8px 14px rgba(0,0,0,0.35);
    overflow: hidden;
  }
  .card--front { top: 67px; background: var(--paper); }
  .card--back  { top: 626px; background: var(--paper-back); }

  .wordmark { position: absolute; color: var(--orange); font-weight: 500; line-height: 1; }
  .wordmark__name { display: block; }
  .wordmark__sub  { display: block; text-align: right; letter-spacing: 2px; }

  .card--front .wordmark { left: 176px; top: 132px; width: 510px; }
  .card--front .wordmark__name { font-size: 150px; letter-spacing: 4px; }
  .card--front .wordmark__sub  { font-size: 44px; margin-top: 6px; }

  .card--back .wordmark { left: 42px; top: 50px; width: 334px; color: var(--ink); }
  .card--back .wordmark__name { font-size: 100px; letter-spacing: 3px; }
  .card--back .wordmark__sub  { font-size: 29px; margin-top: 2px; }

  .address {
    position: absolute; right: 38px; top: 66px;
    text-align: right; font-size: 23px; line-height: 29px; color: var(--ink);
    font-style: normal;
  }
  .person { position: absolute; left: 40px; top: 246px; }
  .person__name { font-size: 31px; font-weight: 600; color: var(--orange); line-height: 1.1; }
  .person__role { font-size: 20px; color: var(--ink); line-height: 1.2; }

  .band { position: absolute; left: 0; top: 0; width: 855px; height: 486px; }

  .contacts {
    position: absolute; right: 38px; top: 324px;
    list-style: none; font-size: 23px; line-height: 34px; color: var(--white);
  }
  .contacts li { display: flex; justify-content: flex-end; align-items: center; gap: 12px; }
  .contacts svg { width: 22px; height: 22px; fill: var(--ink); flex: none; }
</style>
</head>
<body>

<section class="card card--front">
  <div class="wordmark">
    <span class="wordmark__name">kestrel</span>
    <span class="wordmark__sub">BATHROOMS</span>
  </div>
</section>

<section class="card card--back">
  <svg class="band" viewBox="0 0 855 486" aria-hidden="true">
    <path fill="var(--orange)" d="M0,430 C260,470 450,380 600,300 C700,250 780,232 855,238 L855,486 L0,486 Z"/>
  </svg>

  <div class="wordmark">
    <span class="wordmark__name">kestrel</span>
    <span class="wordmark__sub">BATHROOMS</span>
  </div>

  <address class="address">
    Your Adress Inc 2nd Lane<br>Ave Edison, NJ 00000
  </address>

  <div class="person">
    <p class="person__name">Employee Name</p>
    <p class="person__role">Managing Director</p>
  </div>

  <ul class="contacts">
    <li>0012 3456 789
      <svg viewBox="0 0 24 24"><path d="M2 9c0-3 5-5 10-5s10 2 10 5v2h-5V9c-1-.6-3-1-5-1s-4 .4-5 1v2H2z"/><path d="M6 12l2-3h8l2 3v7H6z"/></svg>
    </li>
    <li>0012 3456 789
      <svg viewBox="0 0 24 24"><path d="M7 3h10v5H7z"/><path d="M3 9h18v8h-3v-3H6v3H3z"/><path d="M7 15h10v6H7z"/></svg>
    </li>
    <li>info@youremail.com
      <svg viewBox="0 0 24 24"><path d="M2 5h20v14H2z"/><path d="M3.5 6.5l8.5 7 8.5-7" stroke="#e5762f" stroke-width="1.2" fill="none"/></svg>
    </li>
    <li>www.yourwebsite.com
      <svg viewBox="0 0 24 24"><circle cx="12" cy="12" r="10"/><path d="M2 12h20M12 2v20" stroke="#e5762f" stroke-width="1.4" fill="none"/></svg>
    </li>
  </ul>
</section>

</body>
</html>
```